New Webpage for High Class Expert Witness Services Company

We are looking for a minimalist design for a webpage that just has our logo and an entry form offer to connect with one of our Liaisons.
The entry form should just ask for Name, Email, Contact Info and Description of Project.

Company Name is: The Marlowe Crest Advisory Services

Number of Pages Required

1 page

```html
<!DOCTYPE html>
<html lang="en">
<head>
<meta charset="utf-8">
<title>The Marlowe Crest Advisory Services</title>
<link rel="stylesheet" href="https://fonts.googleapis.com/css2?family=Cinzel:wght@400;600;700&family=Arimo:wght@400;700&display=swap">
<style>
  :root {
    --ink-deep: #111111;
    --hero-light: #4a4a4a;
    --hero-dark: #0c0c0d;
    --text-light: #ffffff;
    --text-soft: #e8e8e8;
    --rule: #b5b5b5;
    --field-bg: #474747;
    --field-line: #8a8a8a;
    --frame-line: #a9a9a9;
    --button-bg: #d3d3d3;
    --button-ink: #1c1c1c;
    --brand-silver: #d6d6d6;
  }
  * { box-sizing: border-box; margin: 0; padding: 0; }
  html, body { width: 848px; height: 1200px; overflow: hidden; }
  body {
    position: relative;
    background: var(--ink-deep);
    font-family: "Arimo", Arial, sans-serif;
    color: var(--text-light);
  }
  .site-header {
    position: absolute; left: 0; top: 0; width: 848px; height: 61px;
    background: var(--ink-deep);
    border-bottom: 1px solid #222;
    display: flex; align-items: center; justify-content: center;
  }
  .brand {
    display: flex; align-items: center; gap: 9px;
    font-family: "Cinzel", serif; font-weight: 600;
    color: var(--brand-silver);
    letter-spacing: 0.06em;
  }
  .brand-mark { background: var(--brand-silver); }
  .site-header .brand { font-size: 17px; }
  .site-header .brand-mark { width: 12px; height: 12px; }
  .hero {
    position: absolute; left: 0; top: 61px; width: 848px; height: 837px;
    background: radial-gradient(ellipse 420px 560px at 424px 300px, var(--hero-light) 0%, #2c2c2c 55%, var(--hero-dark) 100%);
  }
  .hero-inner { position: absolute; inset: 0; text-align: center; }
  .headline {
    position: absolute; left: 0; right: 0; top: 50px;
    font-family: "Cinzel", serif; font-weight: 700;
    font-size: 40px; line-height: 44px; letter-spacing: 0.02em;
  }
  .rule { position: absolute; left: 50%; height: 2px; background: var(--rule); }
  .rule-main { top: 148px; width: 100px; margin-left: -50px; }
  .strapline {
    position: absolute; left: 0; right: 0; top: 171px;
    font-family: "Cinzel", serif; font-weight: 700; font-size: 14px;
    letter-spacing: 0.03em;
  }
  .intro {
    position: absolute; left: 140px; right: 140px;
    font-size: 12.5px; line-height: 22px; color: var(--text-soft);
  }
  .intro strong { font-weight: 700; color: var(--text-light); }
  .intro-first { top: 203px; }
  .intro-second { top: 259px; }
  .form-title {
    position: absolute; left: 0; right: 0; top: 332px;
    font-family: "Cinzel", serif; font-weight: 700; font-size: 19px;
    letter-spacing: 0.02em;
  }
  .rule-form { top: 366px; width: 48px; margin-left: -24px; }
  .consult-form {
    position: absolute; left: 78px; top: 393px; width: 692px; height: 360px;
    border: 1px solid var(--frame-line); border-radius: 6px;
  }
  .field {
    position: absolute;
    background: var(--field-bg);
    border: 1px solid var(--field-line); border-radius: 2px;
    color: var(--text-light);
    font-family: "Arimo", Arial, sans-serif; font-size: 11px;
    padding: 0 12px;
  }
  .field::placeholder { color: var(--text-light); opacity: 1; }
  .field-name { left: 24px; top: 28px; width: 307px; height: 43px; }
  .field-email { left: 360px; top: 28px; width: 307px; height: 43px; }
  .field-contact { left: 24px; top: 99px; width: 643px; height: 43px; }
  .field-project { left: 24px; top: 169px; width: 643px; height: 81px; padding-top: 14px; resize: none; }
  .submit {
    position: absolute; left: 286px; top: 280px; width: 119px; height: 42px;
    background: var(--button-bg); border: none; border-radius: 2px;
    color: var(--button-ink);
    font-family: "Cinzel", serif; font-weight: 700; font-size: 15px; letter-spacing: 0.05em;
  }
  .site-footer {
    position: absolute; left: 0; top: 898px; width: 848px; height: 302px;
    background: var(--ink-deep); text-align: center;
  }
  .site-footer .brand {
    position: absolute; left: 0; right: 0; top: 76px; justify-content: center;
    font-size: 26px;
  }
  .site-footer .brand-mark { width: 18px; height: 18px; }
  .values {
    position: absolute; left: 0; right: 0; top: 162px;
    font-family: "Cinzel", serif; font-weight: 600; font-size: 23px; letter-spacing: 0.02em;
  }
  .values .sep { font-size: 10px; vertical-align: 4px; margin: 0 8px; }
  .copyright {
    position: absolute; left: 0; right: 0; top: 221px;
    font-size: 12px;
  }
</style>
</head>
<body>
  <header class="site-header">
    <div class="brand"><span class="brand-mark"></span>The Marlowe Crest Advisory Services</div>
  </header>

  <section class="hero" role="img" aria-label="Dark backdrop with a faint large emblem and angular facets">
    <div class="hero-inner">
      <h1 class="headline">Elite Expert Witness &amp;<br>Defense Consulting</h1>
      <div class="rule rule-main"></div>
      <p class="strapline">Strategic insight. Courtroom precision. Absolute discretion.</p>
      <p class="intro intro-first"><strong>The Marlowe Crest Advisory Services</strong> provides specialized expert witness and litigation support for complex, high-stakes cases.</p>
      <p class="intro intro-second">The Marlowe Crest Advisory Services provides specialized expert witness and litigation support for complex, high-stakes cases.</p>
      <h2 class="form-title">Request a Confidential Consultation</h2>
      <div class="rule rule-form"></div>
      <form class="consult-form">
        <input class="field field-name" type="text" placeholder="Name">
        <input class="field field-email" type="email" placeholder="Email">
        <input class="field field-contact" type="text" placeholder="Contact Info">
        <textarea class="field field-project" placeholder="Description of Project"></textarea>
        <button class="submit" type="submit">Submit</button>
      </form>
    </div>
  </section>

  <footer class="site-footer">
    <div class="brand"><span class="brand-mark"></span>The Marlowe Crest Advisory Services</div>
    <p class="values">Discreet<span class="sep">&#9656;</span>Secure<span class="sep">&#9656;</span>Professional</p>
    <p class="copyright">&copy; [2026] The Marlowe Crest Advisory Services.All Rights Reserved</p>
  </footer>
</body>
</html>
```